Thornvale Group needs a business card design

We need a new business card design using the logo recently selected in a logo competition on Pixel Bazaar. Our business is a consultancy specializing in aviation and energy and the winning business card design will promote an image of precision and professionalism with creativity.

Please use the logo with the name on the front of the card and use a complementary font. Make the back white with either the light grey or dark grey logo.

Target Market(s)

Senior finance and legal leaders at aviation and energy companies

Industry/Entity Type

Management Consulting

Contact Information for Business Card

Peter Castrell
President
Thornvale Group

www.thornvalegroup.example

(555) 204-6391
pc@thornvalegroup.example

Requirements
Must have
• Professional font that goes well with the logo font

```html
<!DOCTYPE html>
<html lang="en">
<head>
<meta charset="utf-8">
<title>Thornvale Group — Business Card</title>
<link rel="stylesheet" href="https://fonts.googleapis.com/css2?family=Open+Sans:wght@400;700&display=swap">
<style>
  :root {
    --stage: #e9eaee;
    --navy: #123c66;
    --blue-top: #2f77a3;
    --blue-bottom: #0f3f6c;
    --grey-dark: #3f4247;
    --grey-mid: #8f9296;
    --grey-light: #b9bbbe;
    --lavender: #dcdeec;
    --white: #ffffff;
    --accent-blue: #4a86c5;
  }
  * { margin: 0; padding: 0; box-sizing: border-box; }
  html, body {
    width: 1200px; height: 913px; overflow: hidden;
    background: var(--stage);
    font-family: "Open Sans", Arial, sans-serif;
  }
  .canvas { position: relative; width: 1200px; height: 913px; }
  .card {
    position: absolute; width: 560px; height: 320px;
    border-radius: 16px; overflow: hidden;
    box-shadow: 0 10px 30px rgba(20, 30, 50, 0.18);
    background: var(--white);
  }
  .card svg.card-bg { position: absolute; inset: 0; width: 100%; height: 100%; }
  .card-front { left: 70px; top: 90px; }
  .card-back { left: 570px; top: 500px; }

  .holder { position: absolute; left: 32px; top: 138px; }
  .holder-name { color: var(--white); font-weight: 700; font-size: 24px; }
  .holder-title { color: var(--accent-blue); font-size: 16px; margin-top: 2px; }

  .wordmark {
    position: absolute; text-align: center;
    font-weight: 400; text-transform: uppercase; line-height: 1.1;
  }
  .wordmark .line-1 { display: block; font-size: 34px; letter-spacing: 3px; }
  .wordmark .line-2 { display: block; font-size: 16px; letter-spacing: 14px; margin-top: 6px; padding-left: 14px; }
  .wordmark-front { right: 34px; top: 56px; color: var(--white); }
  .mark-square { display: inline-block; width: 22px; height: 22px; background: var(--grey-light); margin-bottom: 14px; }
  .wordmark-back { left: 0; right: 0; top: 160px; color: var(--navy); }
  .wordmark-back .mark-square { background: var(--navy); }

  .contacts {
    position: absolute; right: 32px; top: 196px;
    list-style: none; color: var(--white); font-size: 15px; text-align: right; line-height: 1.55;
  }
  .contacts li { display: flex; justify-content: flex-end; align-items: center; gap: 8px; }
  .contacts svg { width: 13px; height: 13px; flex: none; }
</style>
</head>
<body>
<main class="canvas">

  <section class="card card-front" aria-label="Card front">
    <svg class="card-bg" viewBox="0 0 560 320" preserveAspectRatio="none" aria-hidden="true">
      <defs>
        <linearGradient id="blueFill" x1="0" y1="0" x2="0" y2="1">
          <stop offset="0" stop-color="var(--blue-top)"/>
          <stop offset="1" stop-color="var(--blue-bottom)"/>
        </linearGradient>
        <linearGradient id="greyFill" x1="0" y1="0" x2="0" y2="1">
          <stop offset="0" stop-color="#6d7075"/>
          <stop offset="1" stop-color="var(--grey-dark)"/>
        </linearGradient>
      </defs>
      <rect width="560" height="320" fill="url(#blueFill)"/>
      <polygon points="0,0 205,0 232,320 0,320" fill="url(#greyFill)"/>
      <polygon points="205,0 360,0 232,320" fill="var(--lavender)"/>
    </svg>

    <div class="holder">
      <p class="holder-name">Peter Castrell</p>
      <p class="holder-title">President</p>
    </div>

    <div class="wordmark wordmark-front">
      <span class="mark-square" aria-hidden="true"></span>
      <span class="line-1">Thornvale</span>
      <span class="line-2">Group</span>
    </div>

    <ul class="contacts">
      <li>(555) 204-6391
        <svg viewBox="0 0 16 16" aria-hidden="true"><path d="M4 1l3 3-2 2c1 2 3 4 5 5l2-2 3 3-2 2C7 14 2 9 2 3z" fill="currentColor"/></svg>
      </li>
      <li>pc@thornvalegroup.example
        <svg viewBox="0 0 16 16" aria-hidden="true"><rect x="1" y="3" width="14" height="10" rx="1.5" fill="none" stroke="currentColor" stroke-width="1.6"/><path d="M1.5 4l6.5 5 6.5-5" fill="none" stroke="currentColor" stroke-width="1.6"/></svg>
      </li>
      <li>www.thornvalegroup.example
        <svg viewBox="0 0 16 16" aria-hidden="true"><circle cx="8" cy="8" r="6.5" fill="none" stroke="currentColor" stroke-width="1.5"/><path d="M1.5 8h13M8 1.5c-3 3.5-3 9.5 0 13M8 1.5c3 3.5 3 9.5 0 13" fill="none" stroke="currentColor" stroke-width="1.2"/></svg>
      </li>
    </ul>
  </section>

  <section class="card card-back" aria-label="Card back">
    <svg class="card-bg" viewBox="0 0 560 320" preserveAspectRatio="none" aria-hidden="true">
      <rect width="560" height="320" fill="var(--white)"/>
      <polygon points="0,0 560,0 560,120 0,75" fill="var(--lavender)"/>
      <polygon points="230,0 560,0 560,95" fill="var(--grey-mid)"/>
    </svg>
    <div class="wordmark wordmark-back">
      <span class="mark-square" aria-hidden="true"></span>
      <span class="line-1">Thornvale</span>
      <span class="line-2">Group</span>
    </div>
  </section>

</main>
</body>
</html>
```